A weight loss and fitness website design

I am into different types of modern weight loss techniques for people who are a little fatty and wish to be physically and mentally fit. Basically, the website is to teach people how to reduce weight using different methods such as diet, exercises, yoga and other forms. I would need an eye catching website which would make visitors want to come back. The will be also be different forms of exercises for a health and fit life. This said, my website is to have two categories of
1) weight loss techniques
2) exercise of fit and healthy living.
I prefer bright colors such as green, blue, yellow, and orange. Imagery should include before and after pictures of people suffering from obesity, people under going exercises.
Designers can get ideas and inspiration from the website fitlumen.com which i was previously part of the team.
Target Market(s)
My target audience are people suffering from obesity, malnutrition and physical deficiency.
Industry/Entity Type
Fitness
Coding
Coded - Design and coding required
Number of Pages Required
1 page
Look and feel

```html
<!DOCTYPE html>
<html lang="en">
<head>
<meta charset="utf-8">
<title>Vitora Fitness</title>
<link rel="stylesheet" href="https://fonts.googleapis.com/css2?family=Montserrat:wght@400;500;600;700&family=Open+Sans:ital,wght@0,400;0,600;0,700;1,400&family=Lato:wght@400;700&display=swap">
<style>
:root{
  --green:#14a07f;
  --orange:#f39124;
  --ink:#1c1c1c;
  --text:#3a3a3a;
  --muted:#8c8c8c;
  --light:#a9a9a9;
  --rule:#e4e4e4;
  --white:#ffffff;
  --diet:#17a07f;
  --exercise:#f39124;
  --yoga:#3d6fd1;
}
*{box-sizing:border-box;margin:0;padding:0}
html,body{width:1200px;height:2699px;overflow:hidden;background:var(--white)}
body{position:relative;font-family:"Open Sans",Arial,sans-serif;color:var(--text)}
.abs{position:absolute}
/* header */
.site-header{position:absolute;left:0;top:0;width:1200px;height:79px;background:var(--white)}
.brand{left:97px;top:20px;font-family:"Open Sans",Arial,sans-serif;font-weight:700;font-size:31px;color:var(--green);line-height:40px}
.nav a{position:absolute;top:30px;font-family:"Montserrat",Arial,sans-serif;font-size:14.5px;color:var(--ink);text-decoration:none;font-weight:500}
.btn{position:absolute;display:flex;align-items:center;justify-content:center;gap:8px;color:var(--white);font-family:"Montserrat",Arial,sans-serif;font-size:12.5px}
.btn-orange{background:var(--orange)}
.btn-green{background:var(--green)}
.login{left:929px;top:22px;width:172px;height:34px;font-size:13px;text-transform:uppercase}
/* hero */
.hero{left:0;top:79px;width:1200px;height:549px;background:linear-gradient(90deg,#f1f1f1 0%,#eceeef 35%,#d9e1e6 55%,#e7c3a8 72%,#d9dee3 100%)}
.hero-title{left:90px;top:258px;font-family:"Montserrat",sans-serif;font-weight:600;font-size:35px;color:var(--ink)}
.hero-text{left:90px;top:314px;width:600px;font-family:"Montserrat",sans-serif;font-size:18.5px;line-height:26px;color:var(--ink)}
.quote-btn{left:94px;top:383px;width:163px;height:38px;font-size:15px;font-weight:500}
.dots{left:567px;top:606px;display:flex;gap:8px}
.dots i{width:8px;height:8px;border-radius:50%;background:#d3d3d3}
.dots i:first-child{background:var(--green)}
/* sections */
h2{font-family:"Montserrat",sans-serif;font-weight:500;font-size:32px;color:var(--ink)}
.copy{font-size:12.4px;line-height:18px;color:var(--text)}
.small-btn{height:33px;font-size:11.5px}
.tile{position:absolute;width:99px;height:90px;border:2px solid;display:flex;align-items:center;justify-content:center;background:var(--white)}
.tile-label{position:absolute;font-family:"Open Sans",sans-serif;font-weight:600;font-size:14px;color:var(--ink);text-align:center;width:140px}
.banner{left:0;top:1049px;width:1200px;height:407px;background:linear-gradient(90deg,#c9ccd1 0%,#e6e7e9 25%,#f2f2f2 50%,#ececec 100%)}
.banner-text{right:99px;top:1184px;width:540px;text-align:right;font-family:"Open Sans",sans-serif;font-weight:600;font-size:21px;line-height:26px;color:var(--ink);text-transform:uppercase}
.photo-exercise{left:99px;top:1553px;width:355px;height:267px;background:linear-gradient(120deg,#e9e3dc 0%,#dfe9f2 55%,#b9cde0 100%)}
.testimonials{left:0;top:1894px;width:1200px;height:399px;background:linear-gradient(90deg,#f8f6f2 0%,#f3efe8 45%,#b9b4ad 75%,#3a3636 100%)}
.avatar{left:104px;top:2059px;width:86px;height:86px;border-radius:50%;border:4px solid var(--white);background:#d49a72}
.quote{left:212px;top:2056px;width:340px;font-style:italic;font-size:11.6px;line-height:18px;color:var(--ink)}
.person{left:97px;top:2166px;font-size:13.5px;color:var(--ink)}
.arrows{left:97px;top:2192px;display:flex;gap:3px}
.arrows span{width:16px;height:16px;border-radius:50%;display:flex;align-items:center;justify-content:center}
.compare{left:614px;top:1976px;width:417px;height:265px;background:linear-gradient(90deg,#e8d3c6 0%,#e2cbbd 49%,#222 49.3%,#222 49.7%,#e9d8cc 50%,#4d6c94 100%)}
.compare-label{top:2247px;font-family:"Montserrat",sans-serif;font-size:19px;color:var(--ink)}
/* footer */
.footer h4{position:absolute;font-family:"Lato",sans-serif;font-weight:400;font-size:16px;color:var(--ink)}
.links{position:absolute;list-style:none;font-family:"Lato",sans-serif;font-size:11.5px;line-height:19.8px;color:var(--light)}
.email{left:99px;top:2432px;width:202px;height:39px;background:#ececec;color:#b7b7b7;font-size:13px;padding:11px 14px}
.subscribe{left:301px;top:2432px;width:100px;height:39px;font-size:13px}
.social{left:97px;top:2498px;display:flex;gap:26px}
.social i{width:15px;height:15px;border-radius:50%;background:#9c9c9c}
.social i:nth-child(2){background:#4bb3c8}
.news{position:absolute;font-family:"Lato",sans-serif;font-size:11.5px;line-height:16.5px;color:var(--light);width:200px}
.news b{display:block;color:var(--orange);font-weight:400;margin-top:1px}
.rule{left:76px;top:2639px;width:1040px;height:1px;background:var(--rule)}
.copyright{left:0;top:2662px;width:1200px;text-align:center;font-family:"Lato",sans-serif;font-size:11px;color:var(--muted);letter-spacing:.5px}
</style>
</head>
<body>

<header class="site-header">
  <div class="abs brand">Vitora Fitness</div>
  <nav class="nav">
    <a style="left:437px">Home</a>
    <a style="left:516px">About Us</a>
    <a style="left:615px">Training</a>
    <a style="left:709px">Testimonials</a>
    <a style="left:832px">Contact Us</a>
  </nav>
  <div class="btn btn-orange login">
    <svg width="12" height="12" viewBox="0 0 12 12"><circle cx="6" cy="3.5" r="3" fill="#fff"/><path d="M0 12c0-4 3-5.5 6-5.5s6 1.5 6 5.5z" fill="#fff"/></svg>
    Login / Register
  </div>
</header>

<section>
  <div class="abs hero" role="img" aria-label="Smiling woman punching forward with blue dumbbells in a bright gym"></div>
  <h1 class="abs hero-title">Stay Fit</h1>
  <p class="abs hero-text">We provide modern weight loss techniques for people who are a little fatty and wish to be physically and mentally fit</p>
  <div class="btn btn-green quote-btn">
    <svg width="13" height="13" viewBox="0 0 12 12"><circle cx="6" cy="6" r="6" fill="#fff"/><path d="M5 3.5 7.5 6 5 8.5" stroke="#14a07f" stroke-width="1.6" fill="none"/></svg>
    Get a Quote
  </div>
  <div class="abs dots"><i></i><i></i><i></i><i></i></div>
</section>

<section class="techniques">
  <h2 class="abs" style="left:99px;top:704px">Weight Loss Techniques</h2>
  <p class="abs copy" style="left:99px;top:764px;width:560px">Lorem ipsum dolor sit amet, consectetur adipiscing elit. Quisque fermentum viverra lobortis. Phasellus metus eros, aliquet cursus mauris at, dapibus placerat leo. Cras malesuada ac elit sed auctor. Nulla suscipit porttitor cursus. Aenean eu congue purus. Etiam maximus mattis justo, nec malesuada ipsum elementum a. Etiam quis justo eu urna tempor dictum congue sit amet odio. Lorem ipsum dolor sit amet, consectetur adipiscing elit. Quisque fermentum viverra lobortis. Phasellus metus eros, aliquet cursus mauris at, dapibus placerat leo. Cras malesuada ac elit sed auctor. Nulla suscipit porttitor cursus. Aenean eu congue purus. Etiam maximus mattis justo, nec malesuada ipsum elementum a. Etiam quis justo eu urna tempor dictum congue sit amet odio.</p>
  <div class="btn btn-orange small-btn" style="left:99px;top:948px;width:122px">Read More
    <svg width="10" height="10" viewBox="0 0 12 12"><circle cx="6" cy="6" r="6" fill="#fff"/><path d="M5 3.5 7.5 6 5 8.5" stroke="#f39124" stroke-width="1.6" fill="none"/></svg>
  </div>

  <div class="tile" style="left:761px;top:720px;border-color:var(--diet)">
    <svg width="40" height="40" viewBox="0 0 40 40"><rect x="4" y="10" width="20" height="26" rx="2" fill="none" stroke="#17a07f" stroke-width="3"/><circle cx="27" cy="26" r="9" fill="#17a07f"/><path d="M27 17c0-4 3-6 6-6" stroke="#17a07f" stroke-width="2.5" fill="none"/></svg>
  </div>
  <div class="tile-label" style="left:741px;top:821px">DIET</div>
  <div class="tile" style="left:914px;top:720px;border-color:var(--exercise)">
    <svg width="40" height="40" viewBox="0 0 40 40"><circle cx="24" cy="12" r="7" fill="#f39124"/><circle cx="24" cy="12" r="2.5" fill="#fff"/><rect x="8" y="22" width="18" height="14" rx="2" fill="#f39124"/><rect x="4" y="20" width="5" height="18" rx="1.5" fill="#f39124"/></svg>
  </div>
  <div class="tile-label" style="left:896px;top:821px">EXERCISES</div>
  <div class="tile" style="left:761px;top:866px;border-color:var(--yoga)">
    <svg width="40" height="40" viewBox="0 0 40 40"><circle cx="20" cy="8" r="5" fill="#3d6fd1"/><path d="M14 15h12l2 12H12z" fill="#3d6fd1"/><path d="M4 33c6-5 12-6 16-6s10 1 16 6z" fill="#3d6fd1"/></svg>
  </div>
  <div class="tile-label" style="left:741px;top:966px">YOGA</div>
</section>

<section>
  <div class="abs banner" role="img" aria-label="Woman stretching on a mat in a bright studio"></div>
  <p class="abs banner-text">Nunc dolor sem, mattis et feugiat vitaete mpor et est. Sed at feugiat erat. Etiam non inibus nisi, quis tempus lacus.</p>
  <div class="btn btn-orange small-btn" style="left:979px;top:1299px;width:122px;font-size:11px">View Classes
    <svg width="10" height="10" viewBox="0 0 12 12"><circle cx="6" cy="6" r="6" fill="#fff"/><path d="M5 3.5 7.5 6 5 8.5" stroke="#f39124" stroke-width="1.6" fill="none"/></svg>
  </div>
</section>

<section class="healthy-living">
  <div class="abs photo-exercise" role="img" aria-label="Woman holding blue dumbbells in a gym"></div>
  <h2 class="abs" style="right:99px;top:1537px">Exercise of fit and healthy living</h2>
  <p class="abs copy" style="left:527px;top:1592px;width:574px;text-align:right">Lorem ipsum dolor sit amet, consectetur adipiscing elit. Quisque fermentum viverra lobortis. Phasellus metus eros, aliquet cursus mauris at, dapibus placerat leo. Cras malesuada ac elit sed auctor. Nulla suscipit porttitor cursus. Aenean eu congue purus. Etiam maximus mattis justo, nec malesuada ipsum elementum a. Etiam quis justo eu urna tempor dictum congue sit amet odio. Lorem ipsum dolor sit amet, consectetur adipiscing elit. Quisque fermentum viverra lobortis. Phasellus metus eros, aliquet cursus mauris at, dapibus placerat leo. Cras malesuada ac elit sed auctor. Nulla suscipit porttitor cursus. Aenean eu congue purus. Etiam maximus mattis justo, nec malesuada ipsum elementum a. Etiam quis justo eu urna tempor dictum congue sit amet odio.</p>
  <div class="btn btn-orange small-btn" style="left:977px;top:1778px;width:123px">Read More
    <svg width="10" height="10" viewBox="0 0 12 12"><circle cx="6" cy="6" r="6" fill="#fff"/><path d="M5 3.5 7.5 6 5 8.5" stroke="#f39124" stroke-width="1.6" fill="none"/></svg>
  </div>
</section>

<section>
  <div class="abs testimonials" role="img" aria-label="Soft blurred background of a runner's shoe"></div>
  <h2 class="abs" style="left:97px;top:1982px">Testimonials</h2>
  <div class="abs avatar" role="img" aria-label="Portrait of a client"></div>
  <p class="abs quote">Pellentesque malesuada malesuada urna, ut iaculis massa aliquam eget. Etiam convallis tellus a risus sagittis ullamcorper. In libero sem, malesuada in purus a, vulputate pellentesque dolor. Proin pretium sagittis sapien, a varius ante luctus ac. Phasellus congue tellus ornare, pellentesque neque</p>
  <p class="abs person"><b>Jhon Doe,</b> Lorem ipsum</p>
  <div class="abs arrows">
    <span style="background:#333"><svg width="8" height="8" viewBox="0 0 8 8"><path d="M5 1 2 4l3 3" stroke="#fff" stroke-width="1.5" fill="none"/></svg></span>
    <span style="background:var(--green)"><svg width="8" height="8" viewBox="0 0 8 8"><path d="M3 1l3 3-3 3" stroke="#fff" stroke-width="1.5" fill="none"/></svg></span>
  </div>
  <div class="abs compare" role="img" aria-label="Before and after photos of a waistline in jeans"></div>
  <span class="abs compare-label" style="left:693px">Before</span>
  <span class="abs compare-label" style="left:902px">After</span>
</section>

<footer class="footer">
  <h4 style="left:99px;top:2374px">Subscribe Now</h4>
  <div class="abs email">Your email</div>
  <div class="btn btn-orange subscribe">SUBSCRIBE</div>
  <div class="abs social"><i></i><i></i><i></i><i></i><i></i><i></i></div>

  <h4 style="left:516px;top:2374px">Menu</h4>
  <ul class="links" style="left:516px;top:2409px">
    <li>Home</li><li>About Us</li><li>Gallery</li><li>Services</li><li>Products</li><li>Testimonials</li><li>Contact Us</li>
  </ul>
  <h4 style="left:713px;top:2374px">Useful links</h4>
  <ul class="links" style="left:713px;top:2409px">
    <li>FAQ's</li><li>Privacy Policy</li><li>Terms &amp; Conditions</li><li>Contact Us</li>
  </ul>
  <h4 style="left:911px;top:2374px">Latest News</h4>
  <p class="news" style="left:911px;top:2411px">Pellentesque mauris tortor, lacinia gravida velit eu, faucibus iaculis ligula<b>July 22, 2016</b></p>
  <p class="news" style="left:911px;top:2500px">Pellentesque mauris tortor, lacinia gravida velit eu, faucibus iaculis ligula<b>July 22, 2016</b></p>

  <div class="abs rule"></div>
  <p class="abs copyright">©2016 YOURSITE - ALL RIGHTS RESERVED</p>
</footer>

</body>
</html>
```